Trovanta Overview and Demo Presentation

Objective:
Create a bold, visually engaging PowerPoint deck to present Trovanta’s sales process and system demo to local movers, emphasizing ease of use, increased profitability, and operational efficiency.
Key Elements:
• Design: High-impact graphics with Trovanta branding, minimal text, and clean layouts.
• Content: Step-by-step sales process, key selling points, system demo walkthrough, and a compelling call-to-action.
• Live Demo: Showcase Trovanta’s platform, focusing on instant guaranteed pricing, streamlined booking, and support features.
Deliverables:
A dynamic presentation designed to educate and convert local movers into Trovanta partners, ensuring seamless flow and strong audience engagement.

Target Market(s)

Local Movers

Industry/Entity Type

Household Goods Moving

Font styles to use
Sans Serif

Colors
0054AA
0677BA
7BADD7
CADEEF
E8F1F8
FFC000
F8CF3A
FAE287
FDF2CF
FEFAEE

Requirements
Must have
• Project Brief: Trovanta Sales Process Presentation Objective: Create a bold, visually engaging PowerPoint deck to present Trovanta’s sales process and system demo to local movers, emphasizing ease of use, increased profitability, and operational efficiency. Key Elements: • Design: High-impact graphics with Trovanta branding, minimal text, and clean layouts. • Content: Step-by-step sales process, key selling points, system demo walkthrough, and a compelling call-to-action. • Live Demo: Showcase Trovanta’s platform, focusing on instant guaranteed pricing, streamlined booking, and support features. Deliverables: A dynamic presentation designed to educate and convert local movers into Trovanta partners, ensuring seamless flow and strong audience engagement.

```html
<!DOCTYPE html>
<html lang="en">
<head>
<meta charset="utf-8">
<title>Trovanta Overview Deck</title>
<link href="https://fonts.googleapis.com/css2?family=Poppins:wght@400;500;600&display=swap" rel="stylesheet">
<style>
:root{
  --blue:#2a6be0;
  --blue-deep:#1f58c9;
  --yellow:#fbc332;
  --ink:#222731;
  --muted:#444a55;
  --paper:#ffffff;
  --mist:#f3f5f8;
  --photo-warm-a:#d9c3a0;
  --photo-warm-b:#a97f55;
  --photo-cool-a:#9aa7b6;
  --photo-cool-b:#5c6676;
}
*{margin:0;padding:0;box-sizing:border-box}
html,body{width:1002px;height:1200px;overflow:hidden;background:var(--paper)}
body{position:relative;font-family:'Poppins',sans-serif;color:var(--ink)}
.slide{position:absolute;width:464px;height:262px;background:var(--paper);overflow:hidden;box-shadow:0 1px 4px rgba(0,0,0,.18)}
.slide.tint{background:var(--mist)}
.abs{position:absolute}
.title{position:absolute;font-weight:500;font-size:15.5px;color:var(--blue);line-height:1.3;letter-spacing:.1px}
.title .hl{color:var(--yellow)}
.sub{position:absolute;font-weight:500;font-size:8px;color:var(--ink)}
.body{position:absolute;font-size:7.2px;line-height:16px;color:var(--ink)}
.tiny{position:absolute;font-size:5.2px;line-height:10.5px;color:var(--ink)}
.lab{position:absolute;font-size:6.4px;font-weight:500;color:var(--yellow);letter-spacing:.2px}
.lab.b{color:var(--blue)}
.foot{position:absolute;left:16px;right:16px;top:240px;height:12px;font-size:7px;font-weight:500}
.foot .url{position:absolute;left:0;top:0}
.foot .brand{position:absolute;left:50%;top:-3px;transform:translateX(-50%);font-size:11px;font-weight:600;color:var(--blue);display:flex;align-items:center;gap:4px}
.foot .brand i{display:block;width:8px;height:8px;background:var(--blue)}
.foot .page{position:absolute;right:0;top:0}
.foot .page b{color:var(--blue);font-weight:500;margin-left:6px}
.hex{position:absolute;clip-path:polygon(50% 0,100% 25%,100% 75%,50% 100%,0 75%,0 25%);display:flex;align-items:center;justify-content:center}
.hex.blue{background:var(--blue)}
.hex.yel{background:var(--yellow)}
.photo{position:absolute}
</style>
</head>
<body>

<!-- Cover -->
<section class="slide" style="left:25px;top:31px">
  <svg class="abs" width="464" height="262" style="left:0;top:0">
    <defs>
      <linearGradient id="famGrad" x1="0" y1="0" x2="1" y2="1"><stop offset="0" stop-color="#ece6dc"/><stop offset=".6" stop-color="var(--photo-warm-a)"/><stop offset="1" stop-color="var(--photo-warm-b)"/></linearGradient>
    </defs>
    <polygon points="248,0 464,0 464,150 250,30" fill="var(--blue)"/>
    <polygon points="349,32 437,83 437,185 349,236 261,185 261,83" fill="#fff" stroke="#fff" stroke-width="26" stroke-linejoin="round"/>
    <polygon role="img" aria-label="Photo of a family unpacking moving boxes in their new home" points="349,32 437,83 437,185 349,236 261,185 261,83" fill="url(#famGrad)" stroke="url(#famGrad)" stroke-width="16" stroke-linejoin="round"/>
  </svg>
  <div class="abs" style="left:26px;top:40px;display:flex;align-items:center;gap:8px;font-size:23px;font-weight:600;color:var(--blue)"><i style="display:block;width:16px;height:16px;background:var(--blue)"></i>Trovanta</div>
  <div class="title" style="left:26px;top:92px;font-size:15.5px;line-height:26px">MOVING FOR THE <span class="hl">NEXT</span><br>GENERATION</div>
  <div class="sub" style="left:26px;top:155px;font-size:9.3px;color:var(--muted)">YOUR PARTNER FOR LONG DISTANCE MOVING</div>
  <div class="body" style="left:26px;top:181px;font-size:8px;line-height:21px">From packing to tracking, we take the stress out<br>of your moving experience.</div>
</section>

<!-- Why it matters -->
<section class="slide" style="left:510px;top:31px">
  <div class="title" style="left:15px;top:18px;line-height:22px">WHY DOES <span class="hl">TROVANTA</span><br><span class="hl">MATTER?</span></div>
  <div class="body" style="left:15px;top:67px;font-size:6.8px;line-height:15.5px">Partner with Trovanta and elevate your moving business by<br>expanding your reach and capabilities without the hassle.</div>
  <svg class="photo" role="img" aria-label="Photo of two movers in blue uniforms carrying a sofa" width="190" height="112" style="left:248px;top:4px">
    <defs><linearGradient id="moverGrad" x1="0" y1="0" x2="1" y2="1"><stop offset="0" stop-color="#eef1f6"/><stop offset=".5" stop-color="#c9a38a"/><stop offset="1" stop-color="#3d6ccc"/></linearGradient></defs>
    <ellipse cx="95" cy="64" rx="92" ry="48" fill="url(#moverGrad)" opacity=".8"/>
  </svg>
  <div class="abs" style="left:6px;top:115px;width:452px;height:114px;background:var(--blue);border-radius:0 0 10px 0"></div>
  <div class="abs" style="left:157px;top:118px;width:1px;height:108px;background:rgba(255,255,255,.18)"></div>
  <div class="abs" style="left:308px;top:118px;width:1px;height:108px;background:rgba(255,255,255,.18)"></div>
  <svg class="abs" width="440" height="30" style="left:20px;top:130px" fill="none" stroke="#fff" stroke-width="1">
    <circle cx="12" cy="13" r="6"/><path d="M3 4l5 5M21 4l-5 5M3 24l5-4M21 24l-5-4"/>
    <rect x="158" y="8" width="14" height="14" rx="1"/><path d="M161 18v-4M165 18v-6M169 18v-3"/><circle cx="172" cy="8" r="4"/>
    <rect x="307" y="6" width="20" height="15" rx="2"/><path d="M310 12h14M310 16h10"/>
  </svg>
  <div class="lab" style="left:54px;top:130px;font-size:8px;line-height:15px">MAXIMIZE<br>OPPORTUNITIES</div>
  <div class="lab" style="left:203px;top:138px;font-size:8px">EFFICIENT PRICING</div>
  <div class="lab" style="left:354px;top:130px;font-size:8px;line-height:15px">HASSLE-FREE<br>MANAGEMENT</div>
  <div class="body" style="left:54px;top:163px;color:#fff;font-size:6.5px;line-height:15.3px">Never miss out on another<br>long distance move<br>opportunity again.</div>
  <div class="body" style="left:203px;top:163px;color:#fff;font-size:6.5px;line-height:15.3px">Easily quote competitive<br>pricing and maintain desired<br>profit margins.</div>
  <div class="body" style="left:354px;top:163px;color:#fff;font-size:6.5px;line-height:15.3px">Easily quote competitive<br>pricing and maintain desired<br>profit margins.</div>
  <footer class="foot"><span class="url">HTTPS://TROVANTA.COM/</span><span class="brand"><i></i>Trovanta</span><span class="page">PAGE<b>02</b></span></footer>
</section>

<!-- How it works -->
<section class="slide tint" style="left:25px;top:320px">
  <div class="title" style="left:15px;top:23px">HOW IT <span class="hl">WORKS</span></div>
  <div class="tiny" style="left:182px;top:27px;font-size:5.8px">Trovanta is a tech-driven moving company that automates the move management process.</div>
  <div class="tiny" style="left:10px;top:73px;width:88px;height:132px;background:#fff;border:1px solid #f1e3b8;padding:9px 0 0 7px;line-height:12.8px">Our proprietary technology streamlines the process, offering customers and partners a seamless experience and peace of mind. We have simplified the complex and often stressful task of moving.</div>

  <div class="hex yel" style="left:213px;top:66px;width:43px;height:44px"></div>
  <div class="hex blue" style="left:272px;top:66px;width:43px;height:44px"></div>
  <div class="hex blue" style="left:182px;top:118px;width:43px;height:44px"></div>
  <div class="hex yel" style="left:302px;top:118px;width:43px;height:44px"></div>
  <div class="hex yel" style="left:213px;top:170px;width:43px;height:44px"></div>
  <div class="hex blue" style="left:272px;top:170px;width:43px;height:44px"></div>
  <svg class="abs" width="464" height="262" style="left:0;top:0" fill="none" stroke="#fff" stroke-width="1">
    <path d="M226 97h17M229 97v-7M234 97v-11M239 97v-5M228 84l6-4 6 3"/>
    <rect x="286" y="79" width="14" height="18" rx="1"/><path d="M289 84h8M289 88h8M289 92h5"/>
    <rect x="197" y="131" width="13" height="18" rx="1"/><path d="M200 136h7M200 140h7M200 144h4"/>
    <rect x="315" y="134" width="16" height="12" rx="1"/><path d="M318 134v-4h10v4M320 140h6"/>
    <circle cx="234" cy="192" r="7"/><path d="M234 188v8M232 190h4"/>
    <circle cx="293" cy="192" r="8"/><circle cx="293" cy="192" r="3"/>
  </svg>
  <div class="abs" style="left:238px;top:132px;width:54px;text-align:center;font-size:10px;font-weight:600;color:var(--blue)">Trovanta</div>

  <div class="lab" style="right:267px;top:69px;text-align:right">SPOT AN OPPORTUNITY</div>
  <div class="tiny" style="right:267px;top:81px;text-align:right;font-size:5.6px;line-height:12.5px">Do not let a long-distance move<br>prospect slip away.</div>
  <div class="lab b" style="right:291px;top:121px;text-align:right">GET A QUOTE</div>
  <div class="tiny" style="right:291px;top:133px;text-align:right;font-size:5.6px;line-height:12.5px">Quickly input details on<br>Trovanta.com.</div>
  <div class="lab" style="right:267px;top:175px;text-align:right">SET YOUR PRICE</div>
  <div class="tiny" style="right:267px;top:187px;text-align:right;font-size:5.6px;line-height:12.5px">Offer a suitable price to your<br>customer and secure a deal.</div>

  <div class="lab b" style="left:326px;top:56px">SEAMLESS SCHEDULING</div>
  <div class="tiny" style="left:326px;top:68px">Use Trovanta.com to schedule the service. Just pay<br>the deposit and leave the rest to us. You can even<br>take advantage of our move concierge if that is<br>easier.</div>
  <div class="lab" style="left:356px;top:118px">STAY INFORMED</div>
  <div class="tiny" style="left:356px;top:131px">We ensure constant communication so<br>you can update your customers at every<br>step.</div>
  <div class="lab b" style="left:326px;top:175px">FLEXIBLE PRICING STRUCTURE</div>
  <div class="tiny" style="left:326px;top:187px">You decide the charges. We only bill<br>you, letting you keep your desired<br>profit.</div>
  <footer class="foot"><span class="url">HTTPS://TROVANTA.COM/</span><span class="brand"><i></i>Trovanta</span><span class="page">PAGE<b>03</b></span></footer>
</section>

<!-- About -->
<section class="slide" style="left:510px;top:320px">
  <svg class="abs" width="464" height="262" style="left:0;top:0">
    <defs><linearGradient id="whGrad" x1="0" y1="0" x2="1" y2="1"><stop offset="0" stop-color="#b08a5c"/><stop offset=".5" stop-color="var(--photo-cool-a)"/><stop offset="1" stop-color="var(--photo-cool-b)"/></linearGradient></defs>
    <polygon points="337,0 464,0 464,70 418,88 337,42" fill="var(--yellow)"/>
    <polygon points="413,100 464,70 464,205 413,176" fill="var(--blue)"/>
    <polygon points="339,262 410,205 440,196 464,208 464,262" fill="var(--yellow)"/>
    <polygon role="img" aria-label="Photo of three workers in hard hats talking in a warehouse" points="333,57 408,100 408,186 333,229 258,186 258,100" fill="url(#whGrad)" stroke="url(#whGrad)" stroke-width="14" stroke-linejoin="round"/>
  </svg>
  <div class="title" style="left:26px;top:25px">ABOUT <span class="hl">US</span></div>
  <div class="body" style="left:26px;top:55px;font-size:7px;line-height:16.2px">Trovanta is the next logical evolution in professional moving.<br>Professional moving clients have battled soaring prices,<br>acute capacity problems and deteriorating service levels.</div>
  <div class="body" style="left:26px;top:106px;font-size:7px;line-height:16.2px">Trovanta was founded by lifelong moving professionals who<br>have developed the answer to better moving services.<br>Poised as THE industry disruptor, we deliver faster, offer<br>guaranteed prices and even offer no credit check financing<br>options. We are a technology first organization using<br>proprietary software to deliver moving's best service<br>experience.</div>
  <footer class="foot"><span class="url">HTTPS://TROVANTA.COM/</span><span class="brand"><i></i>Trovanta</span><span class="page">PAGE<b>04</b></span></footer>
</section>

<!-- Traction -->
<section class="slide tint" style="left:25px;top:610px">
  <div class="title" style="left:26px;top:25px">TRACTION</div>
  <div class="sub" style="left:182px;top:29px;font-size:7.6px">WHAT WE'VE ACHIEVED SO FAR</div>
  <div class="photo" role="img" aria-label="Photo of a real estate agent beside a for sale sign" style="left:11px;top:62px;width:107px;height:75px;background:linear-gradient(135deg,#efe9e2,#c9b9a8 55%,#2e4f9a);border-top:2px solid var(--yellow)"></div>
  <div class="photo" role="img" aria-label="Photo of customer support agents wearing headsets" style="left:123px;top:62px;width:107px;height:75px;background:linear-gradient(135deg,#dfe5ec,#8f9aa8 60%,#4b5563);border-bottom:2px solid var(--blue)"></div>
  <div class="photo" role="img" aria-label="Photo of a management team meeting around a table" style="left:235px;top:62px;width:107px;height:75px;background:linear-gradient(135deg,#3a4a44,#6b6a5c 55%,#b08c62);border-top:2px solid var(--yellow)"></div>
  <div class="photo" role="img" aria-label="Photo of a growing vegetable garden" style="left:347px;top:62px;width:107px;height:75px;background:linear-gradient(135deg,#2f4a2a,#5f7d3a 55%,#d4a53a);border-bottom:2px solid var(--blue)"></div>
  <div class="lab b" style="left:11px;top:149px;width:107px;text-align:center;line-height:13px">TECH STACK BUILT AND<br>APPRAISED AT $5M</div>
  <div class="lab b" style="left:123px;top:149px;width:107px;text-align:center">PROVEN B2I MODEL</div>
  <div class="lab b" style="left:235px;top:149px;width:107px;text-align:center">TEAM RESTRUCTURING</div>
  <div class="lab b" style="left:347px;top:149px;width:107px;text-align:center">$1.9M SEED RAISED</div>
  <div class="tiny" style="left:11px;top:178px;width:107px;text-align:center;font-size:5.8px;line-height:13.2px">Trovanta's tech stack is already<br>appraised at $5M, proving our<br>innovation is ready for market</div>
  <div class="tiny" style="left:123px;top:163px;width:107px;text-align:center;font-size:5.8px;line-height:13.2px">Consistent customer<br>acquisition with one new B2I<br>customer per week</div>
  <div class="tiny" style="left:235px;top:163px;width:107px;text-align:center;font-size:5.8px;line-height:13.2px">Brought in a Best-in-Class<br>management team of industry<br>veterans to lead Trovanta into its<br>next growth phase.</div>
  <div class="tiny" style="left:347px;top:163px;width:107px;text-align:center;font-size:5.8px;line-height:13.2px">Used to build the platform<br>and conduct early market<br>tests</div>
  <footer class="foot"><span class="url">HTTPS://TROVANTA.COM/</span><span class="brand"><i></i>Trovanta</span><span class="page">PAGE<b>05</b></span></footer>
</section>

<!-- Corporate relocation -->
<section class="slide tint" style="left:510px;top:610px">
  <div class="title" style="left:22px;top:17px">CORPORATE <span class="hl">RELOCATION</span></div>
  <div class="sub" style="left:22px;top:46px;font-size:7.4px;line-height:15.5px">EXPANDING INTO B2B CORPORATE RELOCATION<br>PARTNERSHIPS</div>
  <div class="hex blue" style="left:21px;top:89px;width:30px;height:34px"></div>
  <div class="hex blue" style="left:21px;top:133px;width:30px;height:34px"></div>
  <div class="hex blue" style="left:21px;top:177px;width:30px;height:34px"></div>
  <svg class="abs" width="60" height="220" style="left:0;top:0" fill="none" stroke="#fff" stroke-width="1">
    <rect x="31" y="98" width="10" height="14" rx="1"/><path d="M33 102h6M33 105h6M33 108h4"/>
    <circle cx="36" cy="148" r="5"/><path d="M36 145v6"/>
    <rect x="30" y="187" width="12" height="14" rx="1"/><path d="M33 197v-3M36 197v-5M39 197v-2"/>
  </svg>
  <div class="body" style="left:71px;top:89px;font-size:7px">Annual Moves from B2B moves/year from<br>secured corporate contracts</div>
  <div class="body" style="left:71px;top:141px;font-size:7px">Estimated Gross Profit</div>
  <div class="body" style="left:71px;top:185px;font-size:7px">Projected EBITDA over the next 24 months</div>
  <div class="body" style="left:264px;top:16px;font-size:7px">After proving the B2I model, Trovanta will concurrently<br>expand into B2B, focusing on corporate relocation<br>services for Fortune 1000 companies. This segment<br>provides high-margin opportunities and long-term<br>contracts.</div>
  <div class="photo" role="img" aria-label="Screenshot of a financial market dashboard with price table and area chart" style="left:265px;top:115px;width:178px;height:90px;background:linear-gradient(180deg,#ffffff 0%,#eef2f8 55%,#cddaf0 100%);border:1.5px solid #9bb2d6;border-radius:3px"></div>
  <footer class="foot"><span class="url">HTTPS://TROVANTA.COM/</span><span class="brand"><i></i>Trovanta</span><span class="page">PAGE<b>06</b></span></footer>
</section>

<!-- Revolutionizing -->
<section class="slide" style="left:25px;top:897px">
  <div class="title" style="left:36px;top:29px">REVOLUTIONIZING</div>
  <div class="sub" style="left:265px;top:34px;font-size:7.6px">THE MOVING INDUSTRY WITH AI</div>
  <div class="body" style="left:36px;top:60px;font-size:7px">Trovanta is transforming the $90-100B moving industry by leveraging AI, GPS, and automated compliance to deliver<br>the first instant guaranteed pricing platform. We're cutting out inefficiencies and middlemen to improve costs and<br>service quality.</div>
  <svg class="abs" width="464" height="262" style="left:0;top:0">
    <path d="M285 100l3.5 2v4L285 108l-3.5-2v-4z" fill="var(--blue)"/>
    <path d="M362 100l3.5 2v4L362 108l-3.5-2v-4z" fill="var(--yellow)"/>
    <g stroke="#9fb6e6" stroke-width=".8" fill="none">
      <path d="M73 144h116M186 142l3 2-3 2"/>
      <path d="M217 144h86M300 142l3 2-3 2"/>
      <path d="M331 144h65M393 142l3 2-3 2"/>
    </g>
  </svg>
  <div class="tiny" style="left:294px;top:99px;font-size:6.8px">TO BUILD</div>
  <div class="tiny" style="left:371px;top:99px;font-size:6.8px">TO PROVE</div>
  <div class="hex blue" style="left:32px;top:126px;width:32px;height:36px;color:#fff;font-size:7.6px;font-weight:500">$1.9M</div>
  <div class="hex blue" style="left:176px;top:126px;width:32px;height:36px;color:#fff;font-size:8.5px;font-weight:500">$5</div>
  <div class="hex yel" style="left:290px;top:126px;width:32px;height:36px;color:#fff;font-size:7.2px;font-weight:500">$500K</div>
  <div class="hex yel" style="left:383px;top:126px;width:32px;height:36px;color:#fff;font-size:7.6px;font-weight:500">B2I</div>
  <div class="sub" style="left:32px;top:176px;font-size:7.4px;font-weight:400;line-height:16px">REVENUE SUCCESSFULLY<br>RAISED</div>
  <div class="sub" style="left:176px;top:176px;font-size:7.4px;font-weight:400;line-height:16px">APPRAISED TECH<br>STACK</div>
  <div class="sub" style="left:290px;top:176px;font-size:7.4px;font-weight:400;line-height:16px">ADDITIONAL<br>RAISE</div>
  <div class="sub" style="left:383px;top:176px;font-size:7.4px;font-weight:400;line-height:16px">SUCCESSFUL<br>MODEL</div>
  <footer class="foot"><span class="url">HTTPS://TROVANTA.COM/</span><span class="brand"><i></i>Trovanta</span><span class="page">PAGE<b>07</b></span></footer>
</section>

<!-- Thank you -->
<section class="slide" style="left:510px;top:897px">
  <svg class="abs" width="464" height="262" style="left:0;top:0">
    <defs><linearGradient id="roomGrad" x1="0" y1="0" x2="1" y2="1"><stop offset="0" stop-color="#f3f1ee"/><stop offset=".55" stop-color="var(--photo-warm-a)"/><stop offset="1" stop-color="var(--photo-warm-b)"/></linearGradient></defs>
    <polygon points="0,0 217,0 217,70 0,195" fill="var(--blue)"/>
    <polygon points="108,27 196,78 196,180 108,231 20,180 20,78" fill="#fff" stroke="#fff" stroke-width="26" stroke-linejoin="round"/>
    <polygon role="img" aria-label="Photo of a bright room with stacked moving boxes and a guitar" points="108,27 196,78 196,180 108,231 20,180 20,78" fill="url(#roomGrad)" stroke="url(#roomGrad)" stroke-width="16" stroke-linejoin="round"/>
  </svg>
  <div class="abs" style="left:252px;top:20px;display:flex;align-items:center;gap:10px;font-size:25px;font-weight:600;color:var(--blue)"><i style="display:block;width:18px;height:18px;background:var(--blue)"></i>Trovanta</div>
  <div class="title" style="left:252px;top:64px;font-size:23px;font-weight:600">THANK <span class="hl">YOU</span></div>
  <div class="hex blue" style="left:252px;top:111px;width:28px;height:31px"><svg width="12" height="12" viewBox="0 0 24 24" fill="#fff"><path d="M6.6 10.8a15.1 15.1 0 006.6 6.6l2.2-2.2c.3-.3.7-.4 1-.2 1.1.4 2.3.6 3.6.6.6 0 1 .4 1 1V20c0 .6-.4 1-1 1A17 17 0 013 4c0-.6.4-1 1-1h3.5c.6 0 1 .4 1 1 0 1.3.2 2.5.6 3.6.1.3 0 .7-.2 1z"/></svg></div>
  <div class="hex blue" style="left:252px;top:159px;width:28px;height:31px"><svg width="12" height="10" viewBox="0 0 24 18" fill="none" stroke="#fff" stroke-width="2"><rect x="1" y="1" width="22" height="16" rx="2"/><path d="M1 2l11 8 11-8"/></svg></div>
  <div class="hex blue" style="left:252px;top:205px;width:28px;height:31px"><svg width="10" height="13" viewBox="0 0 20 26" fill="none" stroke="#fff" stroke-width="2.4"><path d="M10 25s8-8.5 8-14.5a8 8 0 00-16 0C2 16.5 10 25 10 25z"/><circle cx="10" cy="10.5" r="3"/></svg></div>
  <div class="body" style="left:293px;top:118px;font-size:9px">(800) 555-0142</div>
  <div class="body" style="left:293px;top:166px;font-size:9px">SUPPORT@TROVANTA.COM</div>
  <div class="body" style="left:293px;top:204px;font-size:9px;line-height:17px">725 MERIDIAN AVE., #310<br>LARKFIELD CITY, OK 73000</div>
</section>

</body>
</html>
```